Business card design for holistic health care clinic

We need a double-sided business card design for our holistic health care clinic that integrates our logo design and also its color scheme. My business is called Valmira. It is an integrative medicine clinic. You have already done the logo for me. Please ensure an elegant and upscale design that is not cluttered, but still has all the necessary information (please see below for details).

Target Market(s)

Wellness, fitness, rehabilitation for educated, well-traveled open-minded clients who are focused on natural, organic, balanced and preventive healthcare and lifestyle.

Industry/Entity Type

Medical

Contact Information for Business Card

Modern, clean.

Number of Pages Required

1 page

Font styles to use
Serif
Sans Serif

Colors

Designer to choose colors to be used in the design.

Requirements
Must have
• Logo on one side, all other information on the other side.
• Other information should include:
• Tobias Wrenfeld - DOE, CPT, LMT
• 4100 East Marrow Drive
• Austin, TX 78119
• 512 555 0148
• 818 555 0192
• info@ValmiraHealth.example
• t.wrenfeld@ValmiraHealth.example
Nice to have
• Darker background on front - but not totally black - shaded/dark gray.

```html
<!DOCTYPE html>
<html lang="en">
<head>
<meta charset="utf-8">
<title>Valmira – Business Card</title>
<link rel="stylesheet" href="https://fonts.googleapis.com/css2?family=Montserrat:wght@400;600&family=Nunito:wght@700;800&family=Open+Sans:ital,wght@1,600&display=swap">
<style>
  :root {
    --backdrop: #5b4636;
    --card-dark: #242424;
    --card-light: #eeeded;
    --brand-blue: #0b8ac8;
    --text-light: #f1f1f1;
    --text-muted: #4a4a4a;
  }
  * { margin: 0; padding: 0; box-sizing: border-box; }
  html, body {
    width: 1200px;
    height: 808px;
    overflow: hidden;
    background: var(--backdrop);
  }
  .canvas {
    position: relative;
    width: 1200px;
    height: 808px;
  }
  .card {
    position: absolute;
    width: 505px;
    height: 289px;
    overflow: hidden;
  }
  .card--front {
    left: 351px;
    top: 95px;
    background: var(--card-dark);
  }
  .card--back {
    left: 349px;
    top: 398px;
    background: var(--card-light);
  }
  .contact {
    position: absolute;
    left: 0;
    right: 0;
    top: 26px;
    text-align: center;
    font-family: "Montserrat", sans-serif;
    color: var(--text-light);
  }
  .contact__name {
    font-weight: 600;
    font-size: 17px;
    color: var(--brand-blue);
    letter-spacing: 0.3px;
    margin-bottom: 6px;
  }
  .contact__credentials {
    font-size: 10px;
    font-weight: 600;
  }
  .contact__line {
    font-size: 13px;
    font-weight: 400;
    line-height: 16px;
    letter-spacing: 0.2px;
  }
  .contact__line--address { margin-top: 2px; }
  .front-band {
    position: absolute;
    left: 0;
    bottom: 0;
    width: 505px;
    height: 130px;
  }
  .brand {
    position: absolute;
    left: 0;
    right: 0;
    top: 112px;
    text-align: center;
  }
  .brand__name {
    font-family: "Nunito", sans-serif;
    font-weight: 800;
    font-size: 46px;
    line-height: 1;
    color: var(--brand-blue);
    letter-spacing: 1px;
  }
  .brand__descriptor {
    margin-top: 6px;
    font-family: "Nunito", sans-serif;
    font-weight: 700;
    font-size: 15px;
    color: var(--brand-blue);
  }
  .tagline {
    position: absolute;
    left: 0;
    right: 0;
    top: 236px;
    text-align: center;
    font-family: "Open Sans", sans-serif;
    font-style: italic;
    font-weight: 600;
    font-size: 12.5px;
    color: var(--text-muted);
  }
</style>
</head>
<body>
<main class="canvas">
  <section class="card card--front" aria-label="Card front with contact details">
    <div class="contact">
      <p class="contact__name">TOBIAS WRENFELD <span class="contact__credentials">- DOE, CPT, LMT</span></p>
      <p class="contact__line">P : 512 555 0148&nbsp;&nbsp;C : 818 555 0192</p>
      <p class="contact__line">t.wrenfeld@ValmiraHealth.example | www.ValmiraHealth.example</p>
      <p class="contact__line contact__line--address">4100 East Marrow Drive , Austin, TX 78119</p>
    </div>
    <svg class="front-band" viewBox="0 0 505 130" aria-hidden="true">
      <path d="M0 30 Q252 -10 505 30 L505 130 L0 130 Z" fill="var(--brand-blue)"/>
    </svg>
  </section>

  <section class="card card--back" aria-label="Card back with brand name">
    <div class="brand">
      <p class="brand__name">VALMIRA</p>
      <p class="brand__descriptor">Integrative Holistic Medicine</p>
    </div>
    <p class="tagline">it’s all about you – your health, your objectives</p>
  </section>
</main>
</body>
</html>
```